Business card design for Automotive workshop

We need a business card for a new automotive repair and tyre shop called Keelstone Prime Automotive located in New Zealand. We are a clean, modern and fresh workshop and company.

Front needs to feature logo,
my name:
Marlo Fenwicke (director)

Address:
48 Tarn Lane
Rangiwhetu 3592

Phone: 07 594 2713
Mobile: 027 451 9362
Email: office@keelstoneautomotive.example.nz
Website: keelstoneautomotive.example.nz

Back needs to feature an area to write down appointment details, date and time.

Also feature a list of jobs and work we do such as,
Vehicle Servicing
All Mechanical Repairs
Warrant of Fitness
Tyres & Wheel Alignments
Automotive Diagnostics
Automotive Parts & Supplies

```html
<!DOCTYPE html>
<html lang="en">
<head>
<meta charset="utf-8">
<title>Keelstone Prime Automotive – Business Card</title>
<link href="https://fonts.googleapis.com/css2?family=Open+Sans:wght@400;600&family=Roboto:wght@400;500;700&display=swap" rel="stylesheet">
<style>
  :root {
    --bg: #8a8a8a;
    --card: #1c1c1d;
    --red: #e0232e;
    --white: #ffffff;
    --grey: #9a9a9a;
    --logo-grey: #6e6e70;
    --rule: #5a5a5c;
    --dots: #777777;
  }
  * { box-sizing: border-box; margin: 0; padding: 0; }
  html, body { width: 1200px; height: 960px; overflow: hidden; }
  body {
    background: var(--bg);
    font-family: "Open Sans", Arial, sans-serif;
    display: flex; flex-direction: column; align-items: center; justify-content: center;
    gap: 50px;
  }
  .card {
    position: relative;
    width: 640px; height: 390px;
    background: var(--card);
    color: var(--white);
    overflow: hidden;
    box-shadow: 0 10px 24px rgba(0,0,0,.35);
  }

  /* Back: services + appointment */
  .brand-name {
    font-family: "Roboto", Arial, sans-serif;
    font-weight: 700;
    text-transform: uppercase;
    letter-spacing: 2px;
    line-height: 1.05;
  }
  .card-back .brand-name {
    position: absolute; top: 36px; left: 0; right: 0;
    text-align: center; font-size: 38px; color: var(--red);
  }
  .services {
    position: absolute; top: 132px; left: 0; right: 0;
    text-align: center; font-family: "Roboto", Arial, sans-serif;
  }
  .services-title { color: var(--red); font-weight: 500; font-size: 19px; margin-bottom: 8px; }
  .services-list { font-size: 14.5px; line-height: 1.45; color: var(--white); }
  .services-list .dot { color: var(--red); padding: 0 4px; }
  .appointment {
    position: absolute; left: 30px; right: 30px; bottom: 28px; height: 108px;
    background: var(--white);
    padding: 18px 26px;
    display: flex; flex-direction: column; justify-content: space-around;
  }
  .appt-row { display: flex; align-items: flex-end; gap: 8px; font-family: "Roboto", Arial, sans-serif; }
  .appt-label { color: var(--red); font-weight: 500; font-size: 14px; }
  .appt-line { flex: 1; border-bottom: 1.5px dotted var(--dots); height: 1px; margin-bottom: 4px; }
  .appt-line.date { flex: 1.5; }

  /* Front: contact */
  .card-front .brand-name {
    position: absolute; top: 62px; left: 0; right: 0;
    text-align: center; font-size: 34px; color: var(--logo-grey);
  }
  .rule { position: absolute; left: 118px; right: 40px; top: 214px; border-top: 1px solid var(--rule); }
  .person { position: absolute; left: 40px; top: 176px; }
  .person-name { color: var(--red); font-size: 24px; font-weight: 400; line-height: 1.3; }
  .person-role { color: var(--grey); font-size: 16px; margin-top: 2px; }
  .contacts { position: absolute; left: 40px; top: 258px; list-style: none; font-size: 16px; line-height: 1.6; }
  .contacts li { display: flex; align-items: center; gap: 10px; }
  .contacts svg { width: 14px; height: 14px; fill: var(--red); flex: none; }
  .address { position: absolute; right: 40px; top: 226px; text-align: right; font-size: 16px; line-height: 1.6; }
  .edge-stripe { position: absolute; left: 0; right: 0; bottom: 0; height: 24px; }
  .edge-stripe .white { height: 6px; background: var(--white); margin-bottom: 6px; }
  .edge-stripe .red { height: 12px; background: var(--red); }
</style>
</head>
<body>

  <section class="card card-back" aria-label="Card back">
    <div class="brand-name">Keelstone Prime<br>Automotive</div>
    <div class="services">
      <div class="services-title">VEHICLE SERVICING</div>
      <div class="services-list">
        All Mechanical Repairs<span class="dot">•</span>Warrant of Fitness<span class="dot">•</span>Tyres &amp; Wheel Alignments<br>
        Automotive Diagnostics<span class="dot">•</span>Automotive Parts &amp; Supplies
      </div>
    </div>
    <div class="appointment">
      <div class="appt-row"><span class="appt-label">Date:</span><span class="appt-line date"></span><span class="appt-label">Time:</span><span class="appt-line"></span></div>
      <div class="appt-row"><span class="appt-label">Date:</span><span class="appt-line date"></span><span class="appt-label">Time:</span><span class="appt-line"></span></div>
    </div>
  </section>

  <section class="card card-front" aria-label="Card front">
    <div class="brand-name">Keelstone Prime<br>Automotive</div>
    <div class="rule"></div>
    <div class="person">
      <div class="person-name">Marlo Fenwicke</div>
      <div class="person-role">Director</div>
    </div>
    <ul class="contacts">
      <li><svg viewBox="0 0 24 24" aria-hidden="true"><path d="M6.6 10.8a15.1 15.1 0 0 0 6.6 6.6l2.2-2.2c.3-.3.7-.4 1-.2 1.1.4 2.3.6 3.6.6.6 0 1 .4 1 1V20c0 .6-.4 1-1 1A17 17 0 0 1 3 4c0-.6.4-1 1-1h3.5c.6 0 1 .4 1 1 0 1.3.2 2.5.6 3.6.1.3 0 .7-.2 1z"/></svg>07 594 2713</li>
      <li><svg viewBox="0 0 24 24" aria-hidden="true"><path d="M7 1h10a2 2 0 0 1 2 2v18a2 2 0 0 1-2 2H7a2 2 0 0 1-2-2V3a2 2 0 0 1 2-2zm0 3v14h10V4zm5 15.5a1 1 0 1 0 0 2 1 1 0 0 0 0-2z"/></svg>027 451 9362</li>
      <li><svg viewBox="0 0 24 24" aria-hidden="true"><path d="M2 5h20v14H2zm2 2v.5l8 5 8-5V7zm0 2.8V17h16V9.8l-8 5z"/></svg>office@keelstoneautomotive.example.nz</li>
    </ul>
    <div class="address">
      48 Tarn Lane<br>
      Rangiwhetu 3592<br>
      www.keelstoneautomotive.example.nz
    </div>
    <div class="edge-stripe"><div class="white"></div><div class="red"></div></div>
  </section>

</body>
</html>
```